Business card por a urban DJ, up scale audience target

Need a sober design, modern, conservative colors but i can consider some options, y play rnb, hip hop, EDM and top40.

Business card for contact and personal info, double sided, use logo attrached please; im 42 so i need a card acording to my age an target audience.

Target Market(s)

Adult people, up scale audience

Industry/Entity Type

Music Download

Contact Information for Business Card

Cel (318) 4207265518 www.lumadrift.com

Requirements
Must have
• open mind
Nice to have
• open mind
Should not have
• DJ

```html
<!DOCTYPE html>
<html lang="en">
<head>
<meta charset="utf-8">
<title>Luma – Business Card</title>
<link href="https://fonts.googleapis.com/css2?family=Open+Sans:wght@400;700&display=swap" rel="stylesheet">
<style>
  :root {
    --page-bg: #1c1c1e;
    --card-dark: #2c2c2e;
    --card-light: #eceef3;
    --accent-blue: #1f5f8e;
    --arc-dark: #2a2b2e;
    --ink: #1d1d1f;
    --white: #ffffff;
    --rule-light: #8a8a8e;
  }
  * { box-sizing: border-box; margin: 0; padding: 0; }
  html, body { width: 1200px; height: 800px; overflow: hidden; }
  body {
    background: var(--page-bg);
    font-family: "Open Sans", sans-serif;
    display: flex;
    align-items: center;
    justify-content: center;
    gap: 50px;
  }
  .card {
    position: relative;
    width: 525px;
    height: 300px;
    overflow: hidden;
    border-radius: 3px;
  }

  /* Back side */
  .card-back { background: var(--card-dark); }
  .card-back .brand-name {
    position: absolute;
    top: 78px; left: 0; right: 0;
    text-align: center;
    color: var(--white);
    font-weight: 700;
    font-size: 92px;
    letter-spacing: 6px;
    line-height: 1;
  }
  .card-back .back-rule {
    position: absolute;
    height: 1px;
    background: var(--rule-light);
  }
  .card-back .rule-upper { top: 218px; left: 240px; right: 40px; }
  .card-back .rule-lower { top: 248px; left: 130px; right: 160px; }

  /* Front side */
  .card-front { background: var(--accent-blue); }
  .card-front .front-shape { position: absolute; inset: 0; }
  .front-content {
    position: absolute;
    inset: 0;
    text-align: center;
    color: var(--ink);
  }
  .front-content .brand-name {
    position: absolute;
    top: 30px; left: 0; right: 0;
    font-weight: 700;
    font-size: 64px;
    letter-spacing: 4px;
    line-height: 1;
  }
  .person-name {
    position: absolute;
    top: 116px; left: 0; right: 0;
    font-weight: 700;
    font-size: 19px;
  }
  .person-title {
    position: absolute;
    top: 142px; left: 0; right: 0;
    font-size: 13px;
  }
  .front-rule {
    position: absolute;
    top: 166px; left: 64px; right: 64px;
    height: 2px;
    background: var(--ink);
  }
  .contact-list {
    position: absolute;
    top: 180px; left: 0; right: 0;
    list-style: none;
    font-size: 14.5px;
    line-height: 22px;
  }
</style>
</head>
<body>
  <section class="card card-back" aria-label="Card back">
    <div class="brand-name">LUMA</div>
    <div class="back-rule rule-upper"></div>
    <div class="back-rule rule-lower"></div>
  </section>

  <section class="card card-front" aria-label="Card front">
    <svg class="front-shape" width="525" height="300" viewBox="0 0 525 300" aria-hidden="true">
      <path d="M70 -5 Q10 150 70 305 L455 305 Q515 150 455 -5 Z" fill="var(--arc-dark)"/>
      <path d="M84 -5 Q26 150 84 305 L441 305 Q499 150 441 -5 Z" fill="var(--card-light)"/>
    </svg>
    <div class="front-content">
      <div class="brand-name">LUMA</div>
      <div class="person-name">Owen Hartley</div>
      <div class="person-title">Director</div>
      <div class="front-rule"></div>
      <ul class="contact-list">
        <li>(318) 4207265518</li>
        <li>info@lumadrift.com</li>
        <li>www.lumadrift.com</li>
        <li>PO Box 4190 Ashford Vale SA 5071</li>
      </ul>
    </div>
  </section>
</body>
</html>
```